Residential Remodeling Contractor needs updated business card

I need a new design for my business card.
Name of the company is Ridgefell Construction. I need a card that commands presence, strength, integrity. I have been in business for 28 years. I am a Residential Remodeling Contractor that covers all aspects of a residential remodel and build.

```html
<!DOCTYPE html>
<html lang="en">
<head>
<meta charset="utf-8">
<title>Ridgefell Construction — Business Card</title>
<link href="https://fonts.googleapis.com/css2?family=Montserrat:wght@400;500;700&display=swap" rel="stylesheet">
<style>
  :root {
    --backdrop: #2b2b2d;
    --card-blue: #213f80;
    --gloss-blue: #17306a;
    --ink-white: #ffffff;
    --rule-white: rgba(255,255,255,0.9);
  }
  * { box-sizing: border-box; margin: 0; padding: 0; }
  html, body {
    width: 1200px; height: 881px; overflow: hidden;
    background: var(--backdrop);
    font-family: "Montserrat", sans-serif;
  }
  .stage {
    width: 1200px; height: 881px;
    display: flex; align-items: center; justify-content: center; gap: 40px;
  }
  .card {
    width: 560px; height: 320px;
    background: var(--card-blue);
    border-radius: 18px;
    position: relative;
    color: var(--ink-white);
    box-shadow: 0 14px 30px rgba(0,0,0,0.45);
  }
  /* Back side */
  .card-back {
    display: flex; flex-direction: column; align-items: center; justify-content: center;
  }
  .brand-mark {
    display: flex; align-items: center; gap: 12px;
  }
  .brand-mark .mark-dot {
    width: 18px; height: 18px; border-radius: 50%;
  }
  .brand-name {
    font-weight: 700; text-transform: uppercase; line-height: 1.05;
    letter-spacing: 2px;
  }
  .card-back .brand-name { font-size: 34px; color: var(--gloss-blue); }
  .card-back .mark-dot { background: var(--gloss-blue); width: 24px; height: 24px; }
  .tagline {
    margin-top: 34px;
    font-size: 11.5px; font-weight: 500; letter-spacing: 1.6px;
    text-transform: uppercase;
  }
  /* Front side */
  .card-front {
    display: flex; align-items: center;
    padding: 0 34px 0 40px;
  }
  .front-brand { width: 250px; margin-top: 70px; }
  .card-front .brand-name { font-size: 25px; color: var(--ink-white); }
  .card-front .mark-dot { background: var(--ink-white); }
  .divider {
    width: 1.5px; height: 170px; background: var(--rule-white);
    margin: -10px 26px 0 8px;
  }
  .contact { font-size: 12px; font-weight: 400; line-height: 1.35; margin-top: -10px; }
  .person-name { font-size: 19px; font-weight: 700; letter-spacing: 1.8px; text-transform: uppercase; }
  .person-role { font-size: 12px; margin-bottom: 16px; }
  .address { margin-bottom: 14px; }
  .contact-line { display: flex; align-items: center; gap: 7px; }
  .contact-line svg { width: 12px; height: 12px; flex: none; }
</style>
</head>
<body>
<main class="stage">
  <section class="card card-back" aria-label="Card back">
    <div class="brand-mark">
      <span class="mark-dot"></span>
      <div class="brand-name">Ridgefell<br>Construction</div>
    </div>
    <p class="tagline">I have been in business for 28 years</p>
  </section>

  <section class="card card-front" aria-label="Card front">
    <div class="front-brand">
      <div class="brand-mark">
        <span class="mark-dot"></span>
        <div class="brand-name">Ridgefell<br>Construction</div>
      </div>
    </div>
    <div class="divider"></div>
    <div class="contact">
      <p class="person-name">Marcus Delane</p>
      <p class="person-role">Director</p>
      <p class="address">128 Birchwood Lane Athens,<br>GA 30605</p>
      <p class="contact-line">
        <svg viewBox="0 0 24 24" fill="none" stroke="#fff" stroke-width="2.4" stroke-linecap="round"><path d="M5 3h4l2 5-3 2a12 12 0 0 0 6 6l2-3 5 2v4a2 2 0 0 1-2 2A18 18 0 0 1 3 5a2 2 0 0 1 2-2z"/></svg>
        (706) 555-0148
      </p>
      <p class="contact-line">
        <svg viewBox="0 0 24 24" fill="none" stroke="#fff" stroke-width="2.2"><rect x="2" y="5" width="20" height="14" rx="1"/><path d="M2 6l10 7 10-7"/></svg>
        info@ridgefellbuild.com
      </p>
      <p class="contact-line">
        <svg viewBox="0 0 24 24" fill="none" stroke="#fff" stroke-width="2"><circle cx="12" cy="12" r="10"/><path d="M2 12h20M12 2c3 3 3 17 0 20M12 2c-3 3-3 17 0 20"/></svg>
        www.ridgefellbuild.com
      </p>
    </div>
  </section>
</main>
</body>
</html>
```